Printed Circuit Board Company Web Site Design - Please see new file 82012 web design

We are a printed circuit board manufacturer. Need a company professional web site to allow our potential customers to know more about our background, capability and our products. The web site will contain three languages, which are Chinese, English and Japanese. Our audience are mainly electronic companies that procure printed circuit boards. I have a word document that have all the required text in all three languages. The final design should communicate the impression that we embrace quality, trustworthiness and long term partnership business principles.
We should have sections that allow us to post pictures of our facilities.
I have added the three files in three different languages.
Some of the information is below:
Background
RDV Harbourline Limited (RDV) was set up in Hong Kong in 2007 by two Hong Kong entrepreneurs, Mr. Tak Wong and Mr. Lok Fai. We acquired the single sided printed circuit board factory located in Dongguan City, Guangdong Province, China, from Tovand Corporation of the U.S. in 2007. In addition to RDV, Mr. Wong and Mr. Fai also own Halberd Technology Company Limited, a semiconductor company based in Hong Kong since 1997 with a total investment of over US$100 million. Halberd is engaged in the manufacturing of flexible substrates and MEMS assembly business.
RDV has been awarded TS 16949 and ISO14000 certificates since 2009 and 2004 respectively.
Business Principles
RDV Harbourline Limited strives to be a professional top notched printed circuit board supplier. We embrace four “EXCELLENCE” principles, namely, excellence in quality, excellence in prices, excellence in services and excellence in on time delivery.
We approach each customer with a long-term partnership view that delivers the lowest ownership costs and highest total values to our customers. We customize quotations and solutions in order to allow our customers to win more businesses. We believe by thinking from our customers’ points of view we will be able to create a WIN-WIN relationship.
Customers
Due to our excellent quality, services and production systems, RDV Harbourline Limited manage to service a number of large Japanese and US customers, which include:
Technical capability overview
Below is an overview of our current capability:
Target Market(s)
Electronic companies buyers
Industry/Entity Type
Business
Requirements
Must have
- Capability description
Should not have
- no cartoon

```html
<!DOCTYPE html>
<html lang="en">
<head>
<meta charset="utf-8">
<title>RDV Harbourline Limited</title>
<link href="https://fonts.googleapis.com/css2?family=Arimo:wght@400;700&family=Arvo:wght@700&family=Marcellus&family=Marcellus+SC&family=Oswald:wght@300;400&family=Ubuntu+Condensed&display=swap" rel="stylesheet">
<style>
:root{
  --green:#0b7a63;
  --green-dark:#07614e;
  --green-deep:#0a5a48;
  --orange:#f7931e;
  --orange-light:#ffa726;
  --text:#555;
  --field:#efefef;
  --field-border:#d6d6d6;
  --panel:#ebebeb;
  --grey-arrow:#b5b5b5;
}
*{margin:0;padding:0;box-sizing:border-box}
html,body{width:1200px;height:1173px;overflow:hidden;background:#fff}
body{position:relative;font-family:Arimo,Arial,sans-serif;color:var(--text)}
.abs{position:absolute}
.top-bar{left:0;top:0;width:1200px;height:8px;background:var(--green)}
.brand{left:110px;top:22px;color:var(--green);font-family:Arimo,Arial,sans-serif;font-weight:700;line-height:1}
.brand .name{font-size:34px;letter-spacing:2px;display:flex;align-items:center;gap:8px}
.brand .name i{display:inline-block;width:14px;height:14px;background:var(--green)}
.brand .sub{font-size:14px;margin-top:6px;letter-spacing:.5px}
.phone{left:966px;top:66px;display:flex;align-items:center;gap:6px;font-size:12px;color:#222}
.nav{left:99px;top:99px;width:1002px;height:36px;border-radius:5px 5px 0 0;background:linear-gradient(var(--green),var(--green-deep));overflow:hidden}
.nav a{position:absolute;top:9px;color:#fff;text-decoration:none;font-family:"Marcellus SC",serif;font-size:15px;letter-spacing:1px}
.nav .login{right:0;top:0;width:88px;height:36px;background:var(--orange-light);display:flex;align-items:center;justify-content:center;gap:6px;font-family:Arimo,Arial,sans-serif;font-weight:700;font-size:14px;letter-spacing:0;border-radius:0 5px 0 0}
.hero{left:99px;top:135px;width:1002px;height:303px;border:1px solid #8cc3b5;border-top:0;background:linear-gradient(90deg,#eef6f7 0%,#e6f1f4 40%,#cfdfe6 100%);overflow:hidden}
.hero-photo{position:absolute;left:420px;top:0;width:582px;height:303px;background:linear-gradient(135deg,#dfe9ee 0%,#c8d4da 45%,#e9e3dc 75%,#f4f4f2 100%)}
.hero-title{position:absolute;left:0;top:16px;width:380px;text-align:center;font-family:Marcellus,serif;font-size:30px;line-height:36px;color:var(--green)}
.hero-list{position:absolute;left:36px;top:144px;list-style:none}
.hero-list li{display:flex;align-items:center;gap:8px;height:32.5px;font-family:"Ubuntu Condensed",sans-serif;font-size:20px;color:var(--green);letter-spacing:.5px}
.welcome{left:108px;top:476px;font-family:Oswald,sans-serif;font-weight:300;font-size:33px;color:var(--orange);letter-spacing:-.3px}
.intro{left:108px;top:521px;width:617px;font-size:13.6px;line-height:24px;text-align:justify;color:#555}
.intro p+p{margin-top:24px}
.quick{left:776px;top:474px;width:326px;height:342px}
.quick-tab{left:815px;top:474px;width:244px;height:62px;background:linear-gradient(var(--orange-light),var(--orange));border:1px solid #f3b35a;display:flex;align-items:center;justify-content:center;color:#fff;font-family:Arvo,serif;font-weight:700;font-size:22px;letter-spacing:1.5px}
.field{left:810px;width:259px;height:35px;background:linear-gradient(#f4f4f4,#e6e6e6);border:1px solid var(--field-border);padding:9px 12px;font-size:13.5px;color:#777;letter-spacing:.5px}
.submit{left:990px;top:774px;width:79px;height:30px;background:var(--orange);color:#fff;display:flex;align-items:center;justify-content:center;font-family:Arvo,serif;font-weight:700;font-size:12px;letter-spacing:1.5px}
.customers{left:108px;top:853px;width:990px;height:110px;border:1px solid #bdbdbd}
.customers-title{left:124px;top:826px;background:#fff;padding:0 9px;font-family:Oswald,sans-serif;font-weight:400;font-size:25px;color:var(--orange)}
.client{top:885px;height:60px;display:flex;align-items:center;justify-content:center;gap:8px;font-family:Arimo,Arial,sans-serif;font-weight:700;font-size:20px}
.client i{display:inline-block;width:14px;height:14px}
.footer{left:0;top:991px;width:1200px;height:145px;background:linear-gradient(#0b7a63,#07614e)}
.footer-bottom{left:0;top:1136px;width:1200px;height:37px;background:var(--green);display:flex;align-items:center;justify-content:center;color:#fff;font-size:11px;font-weight:700}
.links-title{left:108px;top:1001px;color:#fff;font-weight:700;font-size:12px}
.links{list-style:none;color:#fff;font-size:11px}
.links li{height:18px;line-height:18px;display:flex;align-items:center;gap:5px}
.links li::before{content:"";border-left:4px solid #fff;border-top:2.5px solid transparent;border-bottom:2.5px solid transparent}
.address{right:108px;top:1004px;text-align:right;color:#fff;font-size:11px;line-height:18px}
.address strong{font-size:12px}
</style>
</head>
<body>
<div class="abs top-bar"></div>

<div class="abs brand">
  <div class="name"><i></i>RDV</div>
  <div class="sub">Harbourline Limited</div>
</div>

<div class="abs phone">
  <svg width="30" height="24" viewBox="0 0 30 24"><ellipse cx="14" cy="14" rx="13" ry="9" fill="#0b7a63"/><path d="M9 9c0 5 4 9 9 9l2-2-3-2-1 1c-2-1-3-2-4-4l1-1-2-3z" fill="#fff"/><path d="M22 3c3 1 5 4 5 7" stroke="#0b7a63" stroke-width="2" fill="none"/></svg>
  <span>(852) 2640 1198</span>
</div>

<nav class="abs nav">
  <a style="left:44px">HOME</a>
  <a style="left:161px">PRODUCTS</a>
  <a style="left:314px">SERVICES</a>
  <a style="left:453px">TECHNICAL CAPABILITIES</a>
  <a style="left:721px">CONTACT US</a>
  <a class="login"><svg width="18" height="22" viewBox="0 0 18 22"><path d="M4 10V6a5 5 0 0 1 10 0v4" stroke="#fff" stroke-width="2.5" fill="none"/><rect x="1" y="10" width="16" height="12" rx="2" fill="#fff"/></svg>login</a>
</nav>

<section class="abs hero">
  <div class="hero-photo" role="img" aria-label="Photo of a smiling business team gathered around a meeting table in a bright office"></div>
  <h2 class="hero-title">Our Printed Circuit Board<br>business is committed<br>to "Excellence"</h2>
  <ul class="hero-list">
    <li><svg width="28" height="20" viewBox="0 0 28 20"><path d="M2 11l8 7L27 2" stroke="#0b7a63" stroke-width="3" fill="none"/></svg>EXCELLENCE IN QUALITY</li>
    <li><svg width="28" height="20" viewBox="0 0 28 20"><path d="M2 11l8 7L27 2" stroke="#0b7a63" stroke-width="3" fill="none"/></svg>EXCELLENCE IN PRICES</li>
    <li><svg width="28" height="20" viewBox="0 0 28 20"><path d="M2 11l8 7L27 2" stroke="#0b7a63" stroke-width="3" fill="none"/></svg>EXCELLENCE IN SERVICES</li>
    <li><svg width="28" height="20" viewBox="0 0 28 20"><path d="M2 11l8 7L27 2" stroke="#0b7a63" stroke-width="3" fill="none"/></svg>EXCELLENCE IN ON TIME DELIVERY</li>
  </ul>
</section>

<svg class="abs" style="left:60px;top:236px" width="36" height="90" viewBox="0 0 36 90"><path d="M32 2L6 45l26 43" stroke="#0b7a63" stroke-width="6" fill="none"/></svg>
<svg class="abs" style="left:1103px;top:236px" width="36" height="90" viewBox="0 0 36 90"><path d="M4 2l26 43L4 88" stroke="#0b7a63" stroke-width="6" fill="none"/></svg>

<h1 class="abs welcome">WELCOME TO RDV Harbourline Limited (RDV)</h1>
<div class="abs intro">
  <p>RDV Harbourline Limited (RDV) was set up in Hong Kong in 2007 by two Hong Kong entrepreneurs, Mr. Tak Wong and Mr. Lok Fai. We acquired the single sided printed circuit board factory located in Dongguan City, Guangdong Province, China, from Tovand Corporation of the U.S. in 2007. In addition to RDV, Mr. Wong and Mr. Fai also own Halberd Technology Company Limited, a semiconductor company based in Hong Kong since 1997 with a total investment of over US$100 million. Halberd is engaged in the manufacturing of flexible substrates and the assembly of Micro Electro Mechanical Systems (MEMS).</p>
  <p>RDV has been awarded TS16949 and ISO140001 since 2005 and 2004 respectively.</p>
</div>

<svg class="abs quick" viewBox="0 0 326 342">
  <path d="M20 3H306L323 20V322L306 339H20L3 322V20Z" fill="#fff" stroke="#e3e3e3" stroke-width="4"/>
  <path d="M24 12H302L314 24V318L302 330H24L12 318V24Z" fill="#ebebeb"/>
</svg>
<div class="abs quick-tab">QUICK CONTACT</div>
<div class="abs field" style="top:544px">Name:</div>
<div class="abs field" style="top:584px">Email:</div>
<div class="abs field" style="top:624px">Company Name:</div>
<div class="abs field" style="top:665px;height:101px">Comments:</div>
<div class="abs submit">SUBMIT</div>

<div class="abs customers"></div>
<h2 class="abs customers-title">OUR CUSTOMERS</h2>
<svg class="abs" style="left:82px;top:893px" width="18" height="22" viewBox="0 0 18 22"><path d="M15 2L5 11l10 9" stroke="#b5b5b5" stroke-width="4" fill="none"/></svg>
<svg class="abs" style="left:1104px;top:893px" width="18" height="22" viewBox="0 0 18 22"><path d="M3 2l10 9-10 9" stroke="#b5b5b5" stroke-width="4" fill="none"/></svg>
<div class="abs client" style="left:135px;width:130px;color:#f7931e"><i style="border-radius:50%;background:#f7931e"></i>Norvale</div>
<div class="abs client" style="left:292px;width:150px;color:#1f3f73;font-size:18px">Brantley Power</div>
<div class="abs client" style="left:478px;width:225px;color:#1a7a46"><i style="border-radius:50%;background:#1f5fa8"></i>Keltrix Energy</div>
<div class="abs client" style="left:742px;width:120px;height:63px;top:882px;background:#1a3a72;color:#fff">Mireda</div>
<div class="abs client" style="left:895px;width:165px;color:#1e2a2a;font-size:30px">Tenshu</div>

<footer>
  <div class="abs footer"></div>
  <div class="abs links-title">POPULAR LINKS</div>
  <ul class="abs links" style="left:108px;top:1031px">
    <li>Sitemap</li><li>Circuit Boards</li><li>Capabilities</li><li>Industries Served</li><li>About Us</li>
  </ul>
  <ul class="abs links" style="left:273px;top:1031px">
    <li>Contact Us</li><li>Resources</li><li>Service Center</li><li>News &amp; Events</li><li>Privacy Policy</li>
  </ul>
  <address class="abs address" style="font-style:normal">
    <strong>RDV Harbourline Limited</strong><br>
    12/F Kestrel Plaza<br>
    88 Marlow Road<br>
    Quarry Point, HONG KONG<br>
    Telephone: (852)26401198<br>
    Fax: (852)26401199<br>
    Email: sales@rdvboard.example
  </address>
  <div class="abs footer-bottom">COPYRIGHT © 2012 RDV HARBOURLINE LIMITED. ALL RIGHTS RESERVED</div>
</footer>
</body>
</html>
```